Laser Tattoo Removal Business Cards

We are looking for a professional business card design for a laser tattoo removal business. Ideally looking for a black business card design. The name of the business is Brightline Tattoo Removal. We place our cards at local tattoo shops so we ideally are looking for something trendy/edgy to draw both male and female clientele in.

Target Market(s)

Male/Female ages 18-60

Contact Information for Business Card

black background ideally.. hoping to stay within greys, whites and black

Font styles to use
Serif
Sans Serif

Colors
121212
a9a9a9
5c5c5c
f5f5f5
ffffff
7f7f7f
606060
848484
9d9d9d

Requirements
Must have
• Employee Info:
• Melissa Thornbury
• Chief Executive Offer
• m: 919.537.2846
• w: 919.362.4178
• f: 919.685.3907
• mthornbury@brightlinetattooremoval.example
• Address:
• 4615 Oakmere Pkwy, Suite 210
• Raleigh, NC 27654
• Website:
• www.brightlinetattooremoval.example
Nice to have
• Myabe business name on back or logo on back and employee info on the front

```html
<!DOCTYPE html>
<html lang="en">
<head>
<meta charset="utf-8">
<title>Brightline Tattoo Removal – Business Card</title>
<link href="https://fonts.googleapis.com/css2?family=Roboto:wght@400;700&display=swap" rel="stylesheet">
<style>
  :root {
    --stage: #3b3531;
    --card: #121212;
    --ink: #f5f5f5;
    --white: #ffffff;
    --muted: #a9a9a9;
    --rule: #5c5c5c;
    --gloss: #9d9d9d;
  }
  * { box-sizing: border-box; margin: 0; padding: 0; }
  html, body {
    width: 1200px; height: 769px; overflow: hidden;
    background: var(--stage);
    font-family: "Roboto", sans-serif;
  }
  .canvas { position: relative; width: 1200px; height: 769px; }
  .card {
    position: absolute; top: 236px;
    width: 520px; height: 297px;
    background: var(--card);
    border-radius: 3px;
    box-shadow: 0 14px 30px rgba(0,0,0,.45);
    color: var(--ink);
  }
  .card--front { left: 50px; }
  .card--back { left: 630px; }

  /* front */
  .brand-block {
    position: absolute; left: 0; top: 0; width: 250px; height: 100%;
    display: flex; flex-direction: column; align-items: center; justify-content: center;
  }
  .brand-name {
    font-weight: 700; color: var(--white);
    text-transform: uppercase; text-align: center;
    font-size: 22px; letter-spacing: 3px; line-height: 1.35;
  }
  .brand-name .sub { display: block; font-size: 12px; letter-spacing: 4px; }
  .divider {
    position: absolute; left: 252px; top: 28px; bottom: 28px;
    width: 1px; background: var(--rule);
  }
  .contact {
    position: absolute; left: 268px; top: 40px; width: 240px;
    font-size: 12px; line-height: 1.4; color: var(--ink);
  }
  .contact__name { font-weight: 700; font-size: 17px; text-transform: uppercase; color: var(--white); }
  .contact__title { margin-bottom: 8px; }
  .contact__address { margin-bottom: 8px; }
  .contact__row { display: flex; align-items: center; gap: 7px; height: 17px; }
  .contact__row svg { width: 11px; height: 11px; flex: none; fill: var(--ink); }
  .contact__row--small { font-size: 10.5px; }

  /* back */
  .back-brand {
    position: absolute; left: 0; right: 0; top: 96px; text-align: center;
  }
  .back-brand .brand-name { color: var(--gloss); font-size: 26px; }
  .back-brand .brand-name .sub { font-size: 14px; }
  .back-web {
    position: absolute; left: 0; right: 0; top: 218px; text-align: center;
    font-size: 11px; letter-spacing: 2.5px; color: var(--ink);
  }
</style>
</head>
<body>
<div class="canvas">

  <section class="card card--front">
    <div class="brand-block">
      <p class="brand-name">Brightline<span class="sub">Tattoo Removal</span></p>
    </div>
    <div class="divider"></div>
    <div class="contact">
      <p class="contact__name">Melissa Thornbury</p>
      <p class="contact__title">Chief Executive Offer</p>
      <p class="contact__address">4615 Oakmere Pkwy, Suite 210<br>Raleigh, NC 27654</p>
      <p class="contact__row">
        <svg viewBox="0 0 24 24"><path d="M6.6 10.8a15 15 0 0 0 6.6 6.6l2.2-2.2a1 1 0 0 1 1-.25 11.4 11.4 0 0 0 3.6.57 1 1 0 0 1 1 1V20a1 1 0 0 1-1 1A17 17 0 0 1 3 4a1 1 0 0 1 1-1h3.5a1 1 0 0 1 1 1c0 1.25.2 2.45.57 3.6a1 1 0 0 1-.25 1z"/></svg>919.362.4178
      </p>
      <p class="contact__row">
        <svg viewBox="0 0 24 24"><path d="M7 1h10a2 2 0 0 1 2 2v18a2 2 0 0 1-2 2H7a2 2 0 0 1-2-2V3a2 2 0 0 1 2-2zm0 3v14h10V4zm5 15.5a1.2 1.2 0 1 0 0 2.4 1.2 1.2 0 0 0 0-2.4z"/></svg>919.537.2846
      </p>
      <p class="contact__row">
        <svg viewBox="0 0 24 24"><path d="M6 2h12v5H6zM3 8h18a2 2 0 0 1 2 2v7h-4v5H5v-5H1v-7a2 2 0 0 1 2-2zm4 8v4h10v-4z"/></svg>919.685.3907
      </p>
      <p class="contact__row contact__row--small">
        <svg viewBox="0 0 24 24"><path d="M2 5h20v14H2zm2 2v.5l8 5 8-5V7l-8 5z"/></svg>mthornbury@brightlinetattooremoval.example
      </p>
      <p class="contact__row contact__row--small">
        <svg viewBox="0 0 24 24"><path d="M12 2a10 10 0 1 0 0 20 10 10 0 0 0 0-20zm0 2c1.2 1.4 2 3.5 2.3 6H9.7C10 7.5 10.8 5.4 12 4zm-7.9 8h3.6c.1 2.3.8 4.4 1.9 6A8 8 0 0 1 4.1 12zm5.6 0h4.6c-.2 2.4-1 4.5-2.3 6-1.3-1.5-2.1-3.6-2.3-6zm6.6 0h3.6a8 8 0 0 1-5.5 6c1.1-1.6 1.8-3.7 1.9-6z"/></svg>www.brightlinetattooremoval.example
      </p>
    </div>
  </section>

  <section class="card card--back">
    <div class="back-brand">
      <p class="brand-name">Brightline<span class="sub">Tattoo Removal</span></p>
    </div>
    <p class="back-web">www.brightlinetattooremoval.example</p>
  </section>

</div>
</body>
</html>
```